Smack you in the face - Landing page for Residential Electrical Repairs (Searchly Ads)

I need an effective landing page for Searchly ads. The ads will target residential electrical repairs. Lighting Outages, Power Outages, Breakers Tripping, Outlets Not Working. I need a strong call to action to Call Us Now! Forms don't work well for us so we only need one form as a last option at the bottom of the page. We only work on homes. the website is https://www.vantor-wiring.example/
email is : support@vantor-wiring.example
Phone 555-217-4086

**This is about one focused service. Electrical Repairs - That includes Partial Power Outages, Outlets Not Working, Tripped Breakers, Electrical Panel repairs, and Fusebox Repairs. The area served will only be Greenville, SC. KOBA is the platform

Target Market(s)

Homeonwers in need of electrical repair

Industry/Entity Type

Residential Electricians

Coding

Coded - Design and coding required

Requirements
Must have
• Strong to action for phone calls, this landing page must grab action fast.
Nice to have
• Social proof with existing 5 start reviews for Searchly, Rately, TCB, and Friendnet
Should not have
• Should not be form based. I do not like the site's current them, please don't copy it. Make your own.

```html
<!DOCTYPE html>
<html lang="en">
<head>
<meta charset="utf-8">
<title>Vantor Electrical Service – Residential Electrical Repair</title>
<link rel="stylesheet" href="https://fonts.googleapis.com/css2?family=Michroma&family=Montserrat:ital,wght@0,400;0,500;0,600;0,700;1,500&display=swap">
<style>
:root{
  --blue:#1f8fc2;
  --blue-dark:#16709b;
  --orange:#f26a21;
  --ink:#15171c;
  --navy:#1b1e27;
  --mist:#eef5f8;
  --grey:#555a61;
  --white:#ffffff;
  --star:#f39a1e;
}
*{box-sizing:border-box;margin:0;padding:0}
html,body{width:1200px;height:4208px;overflow:hidden;background:var(--white)}
body{font-family:'Montserrat',sans-serif;color:var(--ink);position:relative}
.abs{position:absolute}
.display{font-family:'Michroma',sans-serif;font-weight:400;line-height:1.15}
.eyebrow{font-family:'Montserrat',sans-serif;font-size:16px;letter-spacing:2.5px;color:var(--blue);text-transform:uppercase;font-weight:500}
.btn{position:absolute;display:flex;align-items:center;justify-content:center;gap:8px;height:56px;width:240px;border-radius:28px;color:var(--white);font-weight:700;font-size:17px;letter-spacing:.5px;text-decoration:none}
.btn svg{width:22px;height:36px}
.btn-blue{background:var(--blue)}
.btn-orange{background:var(--orange)}
.accent{color:var(--blue)}

/* header */
.hero{left:0;top:0;width:1200px;height:735px;overflow:hidden}
.hero-photo{left:0;top:0;width:1200px;height:735px;background:linear-gradient(90deg,#f1f1f1 0%,#ececec 40%,#d9d5cf 65%,#b8aea2 85%,#cfc9c1 100%)}
.topbar{right:0;top:0;height:46px;width:788px}
.topbar-text{top:0;height:46px;display:flex;align-items:center;gap:8px;color:var(--white)}
.addr{left:723px;font-size:10.5px;font-weight:600;line-height:1.2}
.top-phone{left:945px;font-size:16px;font-weight:700}
.logo{left:103px;top:22px;display:flex;align-items:center;gap:10px}
.logo-mark{width:44px;height:44px;border-radius:50%;background:var(--blue)}
.logo-name{font-family:'Michroma',sans-serif;font-size:22px;color:var(--ink);line-height:1}
.logo-sub{display:block;font-family:'Montserrat',sans-serif;font-size:10px;letter-spacing:2px;color:var(--ink);margin-top:4px}
.nav{top:74px;font-size:13px;font-weight:500;letter-spacing:.5px;color:var(--ink)}
.nav.active::after{content:"";position:absolute;left:0;right:0;bottom:-9px;height:2px;background:var(--orange)}
.hero-eyebrow{left:105px;top:226px;font-size:19px}
.hero-title{left:108px;top:254px;padding-left:18px;border-left:3px solid var(--blue);font-size:46px;color:var(--ink);line-height:1.04}

/* about */
.about-photo{left:0;top:833px;width:540px;height:482px}
.about-copy{left:596px;top:852px;width:520px}
.about-copy h2{font-size:34px;margin-top:14px}
.about-copy .rule{width:32px;height:2px;background:var(--orange);margin:14px 0 18px}
.about-copy p{font-size:14.6px;line-height:1.58;color:var(--grey)}
.about-copy p.lead{font-weight:600;color:var(--ink);margin-bottom:18px}

/* call band */
.band{left:0;top:1365px;width:1200px;height:108px}
.band-text{left:147px;top:1365px;height:108px;display:flex;align-items:center;color:var(--white);font-weight:700;font-size:27px;letter-spacing:.3px}
.band-phone{left:846px;top:1365px;height:108px;display:flex;align-items:center;gap:12px;color:var(--white);font-weight:700;font-size:27px}
.phone-dot{width:38px;height:38px;border-radius:50%;background:var(--white);display:flex;align-items:center;justify-content:center}

/* services */
.services{left:0;top:1473px;width:1200px;height:598px;background:var(--mist)}
.center{left:0;width:1200px;text-align:center}
.svc{position:absolute;width:222px;height:222px;border-radius:50%;border:2px solid var(--blue);padding:6px}
.svc-photo{width:100%;height:100%;border-radius:50%;display:flex;align-items:flex-end;justify-content:center;padding-bottom:30px;color:var(--white);font-weight:700;font-size:14px;line-height:1.2;text-align:center;text-shadow:0 1px 3px rgba(0,0,0,.5)}

/* why */
.why-copy{left:144px;top:2170px}
.why-copy h2{font-size:29px;margin-top:12px;line-height:1.25}
.why-item{position:absolute;left:142px;display:flex;align-items:center;gap:22px}
.why-icon{width:62px;height:62px;border-radius:50%;border:2px solid var(--blue);display:flex;align-items:center;justify-content:center}
.why-item strong{font-size:15px;font-weight:700}
.why-item small{display:block;font-size:12px;color:var(--grey);margin-top:3px}
.why-photo{left:645px;top:2144px;width:555px;height:505px}

/* reviews */
.reviews{left:0;top:2714px;width:1200px;height:572px;background:var(--blue);overflow:hidden}
.card{position:absolute;top:181px;width:316px;height:237px;background:var(--white);border-radius:3px;padding:38px 30px 0 36px;box-shadow:0 4px 12px rgba(0,0,0,.12)}
.card.ghost{opacity:.25}
.card q{display:block;font-style:italic;font-size:12.6px;line-height:1.55;color:var(--ink);quotes:"“" "”"}
.card .who{font-weight:700;font-size:13px;margin-top:10px}
.card .stars{color:var(--star);font-size:15px;letter-spacing:1px}
.card .src{position:absolute;right:20px;bottom:20px;font-size:12px;font-weight:700;display:flex;align-items:center;gap:6px}
.card .src i{display:block;width:12px;height:12px;border-radius:50%}
.arrow{position:absolute;top:266px;width:24px;height:40px}

/* contact */
.contact-copy{left:144px;top:3407px}
.contact-copy h2{font-size:32px;margin-top:12px}
.c-item{position:absolute;left:143px;display:flex;align-items:center;gap:16px}
.c-icon{width:56px;height:56px;border-radius:50%;background:var(--blue);display:flex;align-items:center;justify-content:center}
.c-item small{display:block;font-size:15px;color:var(--grey);letter-spacing:.5px}
.c-item b{display:block;font-size:22px;font-weight:700;margin-top:2px}
.c-item span{display:block;font-size:19px;margin-top:4px}
.form{left:606px;top:3380px;width:491px;height:409px;background:var(--blue);border-radius:60px 6px 60px 6px}
.field{position:absolute;left:49px;width:397px;height:42px;border:1.5px solid var(--white);display:flex;align-items:center;gap:10px;padding-left:16px;color:var(--white);font-size:12px}
.field.area{align-items:flex-start;padding-top:12px;height:82px}
.submit{position:absolute;left:46px;top:347px;width:140px;height:36px;border-radius:18px;background:var(--orange);color:var(--white);font-size:12px;font-weight:700;display:flex;align-items:center;justify-content:center}

/* footer */
.footer{left:0;top:3880px;width:1200px;height:328px}
.foot-nav{top:4048px;font-size:16px;font-weight:600;color:var(--white)}
.copy{top:4085px;font-size:12px;color:#c9ccd3}
.social{position:absolute;top:4124px;width:32px;height:32px;border-radius:50%;border:1.5px solid var(--white)}
</style>
</head>
<body>

<!-- HERO -->
<section class="abs hero">
  <div class="abs hero-photo" role="img" aria-label="Photo of a smiling electrician in a white hard hat and safety glasses working on wiring at a service panel"></div>
  <svg class="abs" style="left:0;top:0" width="1200" height="735" viewBox="0 0 1200 735">
    <path d="M0 640 C220 720 520 735 780 690 C960 660 1100 580 1200 520 L1200 735 L0 735Z" fill="var(--white)"/>
    <path d="M200 718 C520 745 820 710 1000 640 C1090 605 1150 570 1200 540" fill="none" stroke="var(--blue)" stroke-width="8"/>
  </svg>
  <svg class="abs topbar" viewBox="0 0 788 46" width="788" height="46">
    <path d="M24 0 H788 V46 H0Z" fill="var(--blue)"/>
    <path d="M258 0 H788 V46 H234Z" fill="var(--orange)"/>
  </svg>
  <div class="abs topbar-text addr">
    <svg width="18" height="22" viewBox="0 0 18 22"><path d="M9 0a8 8 0 0 0-8 8c0 6 8 14 8 14s8-8 8-14a8 8 0 0 0-8-8z" fill="var(--white)"/><circle cx="9" cy="8" r="3" fill="var(--blue)"/></svg>
    <span>418 Birchline Ave, STE 12<br>Raleigh, NC 27600</span>
  </div>
  <div class="abs topbar-text top-phone">
    <svg width="20" height="20" viewBox="0 0 20 20"><circle cx="10" cy="10" r="9" fill="none" stroke="var(--white)" stroke-width="1.5"/><path d="M7 5l2 2-1 2c.8 1.5 1.8 2.5 3 3l2-1 2 2-1.5 1.5C10 14 6 10 5.5 6.5Z" fill="var(--white)"/></svg>
    555-217-4086
  </div>
  <div class="abs logo">
    <span class="logo-mark"></span>
    <div><span class="logo-name">VANTOR</span><span class="logo-sub">ELECTRICAL SERVICE</span></div>
  </div>
  <span class="abs nav active" style="left:390px">HOME</span>
  <span class="abs nav" style="left:498px">ABOUT US</span>
  <span class="abs nav" style="left:637px">ELECTRICAL SERVICES</span>
  <span class="abs nav" style="left:859px">REVIEWS</span>
  <span class="abs nav" style="left:988px">CONTACT US</span>
  <p class="abs eyebrow hero-eyebrow">Vantor Electrical Services</p>
  <h1 class="abs display hero-title">RESIDENTIAL<br>FOR ELECTRICAL<br><span class="accent">REPAIR SOLUTION</span></h1>
  <a class="btn btn-blue" style="left:105px;top:431px" href="tel:5552174086">CALL US NOW
    <svg viewBox="0 0 22 36"><path d="M14 0 L3 20 H11 L7 36 L19 13 H11 Z" fill="var(--white)"/></svg></a>
</section>

<!-- ABOUT -->
<svg class="abs about-photo" viewBox="0 0 540 482" role="img" aria-label="Photo of a smiling electrician in a cap and blue shirt working at a home breaker panel">
  <defs><linearGradient id="aboutG" x1="0" y1="0" x2="1" y2="1"><stop offset="0" stop-color="#e9e6e1"/><stop offset=".55" stop-color="#b9bcc0"/><stop offset="1" stop-color="#4d6f95"/></linearGradient></defs>
  <path d="M0 40 C120 0 300 -5 420 10 C520 25 545 160 530 300 C515 420 450 485 370 480 C250 470 180 390 0 380Z" fill="url(#aboutG)"/>
</svg>
<div class="abs about-copy">
  <p class="eyebrow">Who We Are</p>
  <h2 class="display">ABOUT VANTOR<br><span class="accent">ELECTRICAL REPAIR</span>
    <svg width="22" height="40" viewBox="0 0 22 36" style="vertical-align:-6px"><path d="M14 0 L3 20 H11 L7 36 L19 13 H11 Z" fill="var(--blue)"/></svg></h2>
  <div class="rule"></div>
  <p class="lead">At Vantor Electrical, EV Chargers, &amp; Generators, your electrical emergency is our urgency. We have Licensed Electricians in Greenville, SC, Raleigh, NC, and Charlotte, NC, ensuring top-tier service for every call. We've built our reputation as the go-to Emergency Electrician for homeowners in need.</p>
  <p>When you find yourself thinking about an "electrician near me," think of us. While many electrical contractors chase after large-scale construction and commercial building projects, we prioritize you – the homeowner. We're committed to delivering unbeatable same-day service for all your residential electrical repairs, EV chargers, and Generator installations.</p>
</div>

<!-- CALL BAND -->
<svg class="abs band" viewBox="0 0 1200 108" width="1200" height="108">
  <rect width="1200" height="108" fill="var(--blue)"/>
  <path d="M0 0 H815 L770 108 H0Z" fill="var(--orange)"/>
  <path d="M815 0 L775 56 H800 L752 108 L830 44 H808 L840 0Z" fill="var(--white)"/>
</svg>
<div class="abs band-text">24/7 ELECTRICAL REPAIR SERVICE NOW!</div>
<div class="abs band-phone">
  <span class="phone-dot"><svg width="20" height="20" viewBox="0 0 20 20"><path d="M5 1l4 4-2 3c1.5 2.5 3 4 5 5l3-2 4 4-3 3C9 18 2 11 2 4Z" fill="var(--blue)"/></svg></span>
  555-217-4086
</div>

<!-- SERVICES -->
<section class="abs services">
  <svg class="abs" style="left:588px;top:30px" width="24" height="48" viewBox="0 0 22 36"><path d="M14 0 L3 20 H11 L7 36 L19 13 H11 Z" fill="var(--blue)"/></svg>
  <p class="abs center eyebrow" style="top:90px">What We Do</p>
  <h2 class="abs center display" style="top:114px;font-size:32px">ELECTRICAL <span class="accent">REPAIR</span></h2>
  <div class="svc" style="left:52px;top:204px"><div class="svc-photo" role="img" aria-label="Photo of hands holding pliers at a breaker panel" style="background:linear-gradient(160deg,#a7a29a,#4a4540)">PARTIAL POWER<br>OUTAGES</div></div>
  <div class="svc" style="left:276px;top:204px"><div class="svc-photo" role="img" aria-label="Photo of a hand testing a wall outlet" style="background:linear-gradient(160deg,#dfe3e8,#7a8aa0)">OUTLETS NOT<br>WORKING</div></div>
  <div class="svc" style="left:500px;top:204px"><div class="svc-photo" role="img" aria-label="Photo of an electrician in a cap working on breakers" style="background:linear-gradient(160deg,#c8cbcf,#2a3344)">TRIPPED<br>BREAKERS</div></div>
  <div class="svc" style="left:717px;top:204px"><div class="svc-photo" role="img" aria-label="Photo of an electrician repairing an outdoor electrical panel" style="background:linear-gradient(160deg,#b6b9bb,#4a5058)">ELECTRICAL<br>PANEL REPAIRS</div></div>
  <div class="svc" style="left:939px;top:204px"><div class="svc-photo" role="img" aria-label="Photo of a multimeter testing an old fusebox" style="background:linear-gradient(160deg,#9a8f82,#c9a43a 60%,#3b3631)">FUSEBOX<br>REPAIRS</div></div>
  <a class="btn btn-blue" style="left:500px;top:462px;width:232px" href="tel:5552174086">CALL US NOW
    <svg viewBox="0 0 22 36"><path d="M14 0 L3 20 H11 L7 36 L19 13 H11 Z" fill="var(--white)"/></svg></a>
</section>

<!-- WHY -->
<div class="abs why-copy">
  <p class="eyebrow" style="color:var(--grey)">Why We Are</p>
  <h2 class="display">WHY CHOOSE VANTOR<br>ELECTRICAL SERVICE
    <svg width="20" height="38" viewBox="0 0 22 36" style="vertical-align:-6px"><path d="M14 0 L3 20 H11 L7 36 L19 13 H11 Z" fill="var(--blue)"/></svg></h2>
</div>
<div class="why-item" style="top:2301px">
  <span class="why-icon"><svg width="30" height="30" viewBox="0 0 30 30" fill="none" stroke="var(--blue)" stroke-width="1.6"><rect x="4" y="6" width="22" height="20" rx="2"/><path d="M4 12h22M10 3v6M20 3v6M9 17h2M14 17h2M19 17h2M9 21h2M14 21h2"/></svg></span>
  <div><strong>On-Time Appointments</strong><small>Lorem ipsum dolor sit amet, consectetur</small></div>
</div>
<div class="why-item" style="top:2389px">
  <span class="why-icon"><svg width="32" height="32" viewBox="0 0 32 32" fill="none" stroke="var(--blue)" stroke-width="1.6"><circle cx="16" cy="16" r="12" stroke-dasharray="4 2"/><text x="16" y="20" font-size="9" font-family="Montserrat,sans-serif" font-weight="700" fill="var(--blue)" stroke="none" text-anchor="middle">24/7</text></svg></span>
  <div><strong>Same-Day Service</strong></div>
</div>
<div class="why-item" style="top:2467px">
  <span class="why-icon"><svg width="30" height="30" viewBox="0 0 30 30" fill="none" stroke="var(--blue)" stroke-width="1.6"><circle cx="15" cy="15" r="11"/><circle cx="15" cy="15" r="7"/><path d="M12 15l2 2 4-4"/></svg></span>
  <div><strong>100% Satisfaction Guarantee</strong></div>
</div>
<a class="btn btn-orange" style="left:142px;top:2564px" href="tel:5552174086">CALL US NOW
  <svg viewBox="0 0 22 36"><path d="M14 0 L3 20 H11 L7 36 L19 13 H11 Z" fill="var(--white)"/></svg></a>
<svg class="abs why-photo" viewBox="0 0 555 505" role="img" aria-label="Photo of the company team in navy shirts with families posing in front of a branded service van">
  <defs><linearGradient id="whyG" x1="0" y1="0" x2="1" y2="1"><stop offset="0" stop-color="#6f8a5a"/><stop offset=".45" stop-color="#2c3a78"/><stop offset=".75" stop-color="#1d3b8f"/><stop offset="1" stop-color="#3c4a6e"/></linearGradient></defs>
  <path d="M60 30 C160 0 420 -5 555 30 L555 470 C430 500 250 510 140 485 C40 460 0 380 5 260 C10 140 -10 60 60 30Z" fill="url(#whyG)"/>
</svg>

<!-- REVIEWS -->
<section class="abs reviews">
  <svg class="abs" style="left:588px;top:24px" width="24" height="48" viewBox="0 0 22 36"><path d="M14 0 L3 20 H11 L7 36 L19 13 H11 Z" fill="var(--white)"/></svg>
  <p class="abs center eyebrow" style="top:88px;color:var(--white)">Testimonials</p>
  <h2 class="abs center display" style="top:114px;font-size:32px;color:var(--white)">CUSTOMER REVIEWS</h2>

  <div class="card ghost" style="left:-254px"></div>
  <div class="card" style="left:114px">
    <q>Lorem ipsum dolor sit amet, consectetur adipiscing elit, sed do eiusmod tempor incididunt ut labore et dolore magna aliqua Quis ipsum suspendisse ultrices gravida Risus commodo viverra maecenas</q>
    <p class="who">Dana Morrow</p><p class="stars">★★★★★</p>
    <span class="src"><i style="background:var(--blue)"></i>Searchly</span>
  </div>
  <div class="card" style="left:447px">
    <q>Lorem ipsum dolor sit amet, consectetur adipiscing elit, sed do eiusmod tempor incididunt ut labore et dolore magna aliqua Quis ipsum suspendisse ultrices gravida Risus commodo viverra maecenas</q>
    <p class="who">Dana Morrow</p><p class="stars">★★★★★</p>
    <span class="src"><i style="background:#d32323"></i>Rately</span>
  </div>
  <div class="card" style="left:779px">
    <q>Lorem ipsum dolor sit amet, consectetur adipiscing elit, sed do eiusmod tempor incididunt ut labore et dolore magna aliqua Quis ipsum suspendisse ultrices gravida Risus commodo viverra maecenas</q>
    <p class="who">Dana Morrow</p><p class="stars">★★★★★</p>
    <span class="src"><i style="background:#1877f2"></i>Friendnet</span>
  </div>
  <div class="card ghost" style="left:1138px"></div>

  <svg class="arrow" style="left:70px" viewBox="0 0 24 40"><path d="M18 4 L6 20 L18 36" fill="none" stroke="var(--white)" stroke-width="3"/></svg>
  <svg class="arrow" style="left:1108px" viewBox="0 0 24 40"><path d="M6 4 L18 20 L6 36" fill="none" stroke="var(--white)" stroke-width="3"/></svg>

  <a class="btn btn-orange" style="left:505px;top:451px;width:232px" href="tel:5552174086">CALL US NOW
    <svg viewBox="0 0 22 36"><path d="M14 0 L3 20 H11 L7 36 L19 13 H11 Z" fill="var(--white)"/></svg></a>
</section>

<!-- CONTACT -->
<div class="abs contact-copy">
  <p class="eyebrow">Get In Touch</p>
  <h2 class="display">CONTACT <span class="accent">US</span>
    <svg width="20" height="38" viewBox="0 0 22 36" style="vertical-align:-2px"><path d="M14 0 L3 20 H11 L7 36 L19 13 H11 Z" fill="var(--blue)"/></svg></h2>
</div>
<div class="c-item" style="top:3511px">
  <span class="c-icon"><svg width="22" height="28" viewBox="0 0 18 22"><path d="M9 0a8 8 0 0 0-8 8c0 6 8 14 8 14s8-8 8-14a8 8 0 0 0-8-8z" fill="var(--white)"/><circle cx="9" cy="8" r="3" fill="var(--blue)"/></svg></span>
  <div><small>AREA SERVE</small><b>Greenville</b></div>
</div>
<div class="c-item" style="top:3597px">
  <span class="c-icon"><svg width="26" height="26" viewBox="0 0 20 20"><path d="M5 1l4 4-2 3c1.5 2.5 3 4 5 5l3-2 4 4-3 3C9 18 2 11 2 4Z" fill="var(--white)"/></svg></span>
  <div><small>PHONE NUMBER</small><b>555-217-4086</b></div>
</div>
<div class="c-item" style="top:3685px">
  <span class="c-icon"><svg width="28" height="20" viewBox="0 0 28 20" fill="none" stroke="var(--white)" stroke-width="2"><rect x="1" y="1" width="26" height="18" rx="2"/><path d="M1 2l13 10L27 2M1 18l9-8M27 18l-9-8"/></svg></span>
  <div><small>EMAIL US</small><span>support@vantor-wiring.example</span></div>
</div>

<form class="abs form" action="#">
  <div class="field" style="top:44px"><svg width="12" height="12" viewBox="0 0 12 12"><circle cx="6" cy="3.5" r="3" fill="var(--white)"/><path d="M0 12c0-4 3-5 6-5s6 1 6 5Z" fill="var(--white)"/></svg>First name</div>
  <div class="field" style="top:98px"><svg width="12" height="12" viewBox="0 0 12 12"><circle cx="6" cy="3.5" r="3" fill="var(--white)"/><path d="M0 12c0-4 3-5 6-5s6 1 6 5Z" fill="var(--white)"/></svg>Last name</div>
  <div class="field" style="top:152px"><svg width="12" height="12" viewBox="0 0 20 20"><path d="M5 1l4 4-2 3c1.5 2.5 3 4 5 5l3-2 4 4-3 3C9 18 2 11 2 4Z" fill="var(--white)"/></svg>Phone number</div>
  <div class="field" style="top:206px"><svg width="14" height="10" viewBox="0 0 28 20"><rect x="0" y="0" width="28" height="20" rx="2" fill="var(--white)"/><path d="M1 2l13 10L27 2" fill="none" stroke="var(--blue)" stroke-width="2"/></svg>Email address</div>
  <div class="field area" style="top:253px">Comments</div>
  <div class="submit">SUBMIT ›</div>
</form>

<!-- FOOTER -->
<svg class="abs footer" viewBox="0 0 1200 328" width="1200" height="328">
  <path d="M0 95 C260 20 620 0 880 35 C1020 55 1130 80 1200 105 L1200 328 L0 328Z" fill="var(--navy)"/>
  <path d="M0 90 C260 10 620 -8 880 25 C1020 45 1130 70 1200 95" fill="none" stroke="var(--blue)" stroke-width="8"/>
</svg>
<div class="abs" style="left:0;top:3960px;width:1200px;display:flex;justify-content:center;align-items:center;gap:10px">
  <span class="logo-mark" style="width:36px;height:36px"></span>
  <div><span class="logo-name" style="color:var(--white);font-size:20px">VANTOR</span><span class="logo-sub" style="color:var(--white);font-size:9px">ELECTRICAL SERVICE</span></div>
</div>
<span class="abs foot-nav" style="left:241px">HOME</span>
<span class="abs foot-nav" style="left:371px">ABOUT US</span>
<span class="abs foot-nav" style="left:534px">SERVICES</span>
<span class="abs foot-nav" style="left:693px">REVIEWS</span>
<span class="abs foot-nav" style="left:847px">CONTACT US</span>
<p class="abs center copy">© 2023 <u>Vantor Electrical Service.</u> All Right Reserved</p>
<span class="social" style="left:557px" aria-label="Friendnet"></span>
<span class="social" style="left:598px" aria-label="Social profile"></span>
<span class="social" style="left:637px" aria-label="Social profile"></span>

</body>
</html>
```